FinTech company looking to revamp and expand client-facing interface for our financial models

Pellworth Engines currently has a very simple website that allows clients to interact with our financial models. We are looking to completely redesign the current site and add several extra pages to provide extra functionality. We want the design to have a modern, slick feel, that will work on both a desktop or a tablet. It should be straightforward for clients to move between different pages at any time, and clear from the layout how to interact with the more advanced features. We have included screenshots of existing pages in the attached design brief, as well as sketches of the functionality required by the new pages, but can't provide a direct link to the current site.
Target Market(s)
Professional investors that will be paying to access the interface
Industry/Entity Type
Finance
Number of Pages Required
4 page
Colors
Designer to choose colors to be used in the design.
Look and feel
Each slider illustrates characteristics of the customer's brand and the style your logo design should communicate.

```html
<!DOCTYPE html>
<html lang="en">
<head>
<meta charset="utf-8">
<title>Pellworth Engines · Backtest</title>
<link href="https://fonts.googleapis.com/css2?family=Open+Sans:wght@400;600;700&family=Roboto+Condensed:wght@400;500&display=swap" rel="stylesheet">
<style>
:root{
  --navy:#0d2f5f;
  --teal:#0f6e6a;
  --ink:#111;
  --black:#1a1a1a;
  --page:#e8e8e8;
  --frame:#f4f4f4;
  --row-alt:#efefef;
  --white:#fff;
  --muted:#666;
  --blue:#3a6fb0;
  --olive:#b5b532;
  --green:#3a9a3a;
}
*{box-sizing:border-box;margin:0;padding:0}
html,body{width:1200px;height:1122px;overflow:hidden;background:var(--frame)}
body{font-family:"Open Sans",sans-serif;color:var(--ink)}
.stage{position:relative;width:1300px;height:1215px;transform:scale(0.92308);transform-origin:0 0;background:var(--frame)}
.abs{position:absolute}
.app{left:15px;top:15px;width:1270px;height:1185px;background:var(--page)}
.app-lower{left:15px;top:560px;width:1270px;height:640px;background:#f6f6f6}
/* nav */
.nav{left:15px;top:15px;width:1270px;height:60px;background:var(--white);display:flex;align-items:stretch}
.brand{width:180px;display:flex;align-items:center;padding-left:58px;font-weight:700;font-size:18px}
.nav-cell{display:flex;align-items:center;justify-content:center;gap:8px;font-weight:700;font-size:13.5px;border-left:1px solid #e4e4e4}
.nav-spacer{border-left:1px solid #e4e4e4}
.nav-cell.active{background:var(--navy);color:var(--white)}
/* chart card */
.card{left:105px;top:115px;width:1160px;height:425px;background:var(--white);box-shadow:0 2px 6px rgba(0,0,0,.08)}
.card-head{left:105px;top:115px;width:1160px;height:85px;background:#efefef}
.tab{top:160px;height:40px;display:flex;align-items:center;justify-content:center;font-size:12px;font-weight:600;color:#444}
.tab.light{background:var(--white)}
.tab.dark{background:var(--black);color:var(--white)}
.chart{left:105px;top:200px}
/* overlay panel */
.panel{left:15px;top:155px;width:490px;height:610px;background:rgba(28,28,28,.9);color:var(--white)}
.handle{left:505px;top:335px;width:50px;height:250px;background:rgba(28,28,28,.9);border-radius:0 4px 4px 0}
.handle-text{left:505px;top:335px;width:50px;height:250px;display:flex;align-items:center;justify-content:center}
.handle-text span{transform:rotate(-90deg);white-space:nowrap;font-size:16px;font-weight:600;letter-spacing:.5px;color:var(--white)}
.handle-btn{left:541px;top:446px}
.btn{display:flex;align-items:center;justify-content:center;color:var(--white);font-weight:600}
.mode{top:230px;width:180px;height:45px;font-size:16px;border:2px solid var(--white)}
.mode.on{background:var(--navy)}
.label{font-weight:700;font-size:17px;color:var(--white)}
.select{left:150px;top:305px;width:180px;height:30px;background:var(--white);color:var(--ink);font-size:15px;display:flex;align-items:center;padding-left:12px;border-radius:2px}
.select-btn{left:340px;top:305px;width:105px;height:30px;background:var(--teal);font-size:15px;border:1px solid #cde;border-radius:2px}
.add{left:75px;top:355px;width:195px;height:40px;background:var(--navy);font-size:13.5px;gap:12px;border-radius:2px}
.field{left:175px;width:270px;height:30px;background:var(--white);color:var(--ink);font-size:15px;display:flex;align-items:center;padding-left:12px;border-radius:3px}
/* tables */
.tbl{font-family:"Roboto Condensed",sans-serif;font-size:17px}
.thead{height:70px;background:var(--black);color:var(--white)}
.cell{position:absolute;display:flex;align-items:center;justify-content:center;height:70px}
.hcell{font-family:"Open Sans",sans-serif;font-weight:600;font-size:17px;border-left:1px solid #333}
.row{position:absolute;height:70px}
.row.alt{background:var(--row-alt)}
.row.plain{background:var(--white)}
.track{width:40px;background:#dedede}
.pill{position:absolute;left:11px;width:18px;border-radius:9px;background:linear-gradient(#5a5a5a,#000 70%)}
.thumb{position:absolute;left:12px;width:16px;height:70px;border-radius:8px;background:#8a8a8a}
.run{left:182px;top:640px;width:155px;height:50px;background:var(--navy);border:2px solid var(--white);border-radius:3px;font-size:16px;font-weight:700}
.export{top:593px;display:flex;align-items:center;gap:8px;font-weight:700;font-size:17px;color:var(--navy)}
</style>
</head>
<body>
<div class="stage">
  <div class="abs app"></div>
  <div class="abs app-lower"></div>

  <nav class="abs nav">
    <div class="brand">PELLWORTH</div>
    <div class="nav-cell" style="width:90px">250D</div>
    <div class="nav-cell" style="width:90px">83D</div>
    <div class="nav-cell" style="width:90px">42D</div>
    <div class="nav-spacer" style="width:135px"></div>
    <div class="nav-cell" style="width:140px">
      <svg width="24" height="22" viewBox="0 0 24 22"><path d="M2 11 12 2l10 9h-3v10h-5v-6h-4v6H5V11z" fill="#111"/></svg>MODELS</div>
    <div class="nav-cell" style="width:178px">
      <svg width="24" height="24" viewBox="0 0 24 24" fill="none" stroke="#111" stroke-width="1.6"><circle cx="12" cy="12" r="4"/><circle cx="12" cy="12" r="9" stroke-dasharray="2 2.4"/></svg>SENSITIVITIES</div>
    <div class="nav-cell" style="width:160px">
      <svg width="24" height="24" viewBox="0 0 24 24" fill="none" stroke="#111" stroke-width="1.8"><circle cx="6" cy="6" r="4"/><circle cx="18" cy="6" r="4"/><circle cx="6" cy="18" r="4"/><circle cx="18" cy="18" r="4"/></svg>PORTFOLIO</div>
    <div class="nav-cell active" style="width:152px">
      <svg width="26" height="22" viewBox="0 0 26 22" fill="none" stroke="#fff" stroke-width="1.8"><rect x="1.5" y="1.5" width="23" height="19"/><path d="M5 15l5-6 4 4 6-7"/></svg>BACKTEST</div>
  </nav>

  <div class="abs card"></div>
  <div class="abs card-head"></div>
  <div class="abs tab dark" style="left:160px;width:155px">CHART</div>
  <div class="abs tab" style="left:315px;width:100px">#1</div>
  <div class="abs tab" style="left:415px;width:90px">#2</div>
  <div class="abs tab light" style="left:510px;width:90px">#3</div>
  <div class="abs tab dark" style="left:605px;width:90px">#4</div>

  <svg class="abs chart" width="1160" height="340" viewBox="105 200 1160 340" role="img" aria-label="Backtest scatter chart">
    <g stroke="#e6e6e6" stroke-width="1">
      <line x1="185" y1="263" x2="1110" y2="263"/><line x1="185" y1="300" x2="1110" y2="300"/>
      <line x1="185" y1="338" x2="1110" y2="338"/><line x1="185" y1="375" x2="1110" y2="375"/>
      <line x1="185" y1="412" x2="1110" y2="412"/>
    </g>
    <line x1="185" y1="449" x2="1110" y2="449" stroke="#777"/>
    <g font-family="Open Sans, sans-serif" font-size="12" fill="#666" text-anchor="middle">
      <text x="180" y="303">80</text><text x="180" y="341">60</text><text x="180" y="416">20</text><text x="180" y="453">0</text>
      <text x="360" y="476">Sep 2018</text><text x="500" y="476">Nov 2018</text><text x="640" y="476">Jan 2019</text>
      <text x="777" y="476">Mar 2019</text><text x="917" y="476">May 2019</text><text x="1057" y="476">Jul 2019</text>
    </g>
    <g fill="var(--olive)">
      <circle cx="270" cy="263" r="3.5"/><circle cx="290" cy="263" r="3.5"/><circle cx="310" cy="263" r="3.5"/><circle cx="330" cy="264" r="3.5"/><circle cx="350" cy="263" r="3.5"/><circle cx="372" cy="290" r="3.5"/><circle cx="390" cy="330" r="3.5"/><circle cx="410" cy="362" r="3.5"/><circle cx="440" cy="265" r="3.5"/><circle cx="455" cy="340" r="3.5"/><circle cx="470" cy="300" r="3.5"/>
      <circle cx="565" cy="337" r="3.5"/><circle cx="571" cy="348" r="3.5"/><circle cx="578" cy="265" r="3.5"/><circle cx="588" cy="264" r="3.5"/><circle cx="598" cy="266" r="3.5"/>
      <circle cx="612" cy="438" r="3.5"/><circle cx="628" cy="436" r="3.5"/><circle cx="636" cy="432" r="3.5"/><circle cx="645" cy="426" r="3.5"/><circle cx="656" cy="430" r="3.5"/><circle cx="665" cy="435" r="3.5"/><circle cx="675" cy="438" r="3.5"/><circle cx="680" cy="410" r="3.5"/><circle cx="688" cy="398" r="3.5"/><circle cx="696" cy="378" r="3.5"/><circle cx="693" cy="365" r="3.5"/>
      <circle cx="690" cy="326" r="3.5"/><circle cx="703" cy="326" r="3.5"/><circle cx="708" cy="290" r="3.5"/><circle cx="724" cy="285" r="3.5"/><circle cx="740" cy="297" r="3.5"/><circle cx="745" cy="320" r="3.5"/><circle cx="753" cy="320" r="3.5"/><circle cx="756" cy="363" r="3.5"/><circle cx="730" cy="407" r="3.5"/><circle cx="737" cy="418" r="3.5"/><circle cx="726" cy="340" r="3.5"/>
      <circle cx="760" cy="273" r="3.5"/><circle cx="770" cy="283" r="3.5"/><circle cx="778" cy="270" r="3.5"/><circle cx="788" cy="274" r="3.5"/>
      <circle cx="805" cy="266" r="3.5"/><circle cx="840" cy="266" r="3.5"/><circle cx="880" cy="267" r="3.5"/><circle cx="920" cy="266" r="3.5"/><circle cx="960" cy="267" r="3.5"/><circle cx="1000" cy="267" r="3.5"/><circle cx="1020" cy="266" r="3.5"/>
    </g>
    <g fill="var(--blue)">
      <circle cx="280" cy="390" r="3.5"/><circle cx="300" cy="370" r="3.5"/><circle cx="325" cy="380" r="3.5"/><circle cx="345" cy="400" r="3.5"/><circle cx="375" cy="428" r="3.5"/><circle cx="400" cy="425" r="3.5"/><circle cx="430" cy="395" r="3.5"/><circle cx="470" cy="420" r="3.5"/><circle cx="495" cy="410" r="3.5"/>
      <circle cx="512" cy="285" r="3.5"/><circle cx="516" cy="300" r="3.5"/><circle cx="526" cy="298" r="3.5"/><circle cx="518" cy="274" r="3.5"/>
      <circle cx="558" cy="410" r="3.5"/><circle cx="564" cy="382" r="3.5"/><circle cx="568" cy="368" r="3.5"/><circle cx="575" cy="370" r="3.5"/>
      <circle cx="578" cy="284" r="3.5"/><circle cx="583" cy="278" r="3.5"/><circle cx="590" cy="270" r="3.5"/><circle cx="598" cy="273" r="3.5"/><circle cx="606" cy="280" r="3.5"/><circle cx="614" cy="266" r="3.5"/>
    </g>
    <line x1="625" y1="263" x2="1062" y2="263" stroke="var(--blue)" stroke-width="7" stroke-linecap="round" stroke-dasharray="0.1 8"/>
    <g fill="var(--green)"><circle cx="1035" cy="446" r="3.5"/><circle cx="1040" cy="446" r="3.5"/><circle cx="1046" cy="446" r="3.5"/></g>
    <text x="1167" y="265" font-family="Georgia, serif" font-size="12" fill="#333">Names</text>
    <g>
      <circle cx="1150" cy="261" r="3.5" fill="#8fb3d9"/><circle cx="1150" cy="280" r="3.5" fill="#f2b37a"/><circle cx="1150" cy="299" r="3.5" fill="#3a9a3a"/><circle cx="1150" cy="317" r="3.5" fill="#e07f8a"/><circle cx="1150" cy="336" r="3.5" fill="#c8a9d8"/><circle cx="1150" cy="355" r="3.5" fill="#b89a8a"/><circle cx="1150" cy="373" r="3.5" fill="#e8a9cc"/><circle cx="1150" cy="392" r="3.5" fill="#bdbdbd"/><circle cx="1150" cy="411" r="3.5" fill="#b5b532"/><circle cx="1150" cy="429" r="3.5" fill="#7fd3e0"/><circle cx="1150" cy="448" r="3.5" fill="#3a6fb0"/>
    </g>
  </svg>

  <!-- stats table -->
  <div class="tbl">
    <div class="abs thead" style="left:105px;top:630px;width:400px"></div>
    <div class="row plain" style="left:105px;top:700px;width:360px"></div>
    <div class="row alt" style="left:105px;top:770px;width:360px"></div>
    <div class="row plain" style="left:105px;top:840px;width:360px"></div>
    <div class="row alt" style="left:105px;top:910px;width:360px"></div>
    <div class="row plain" style="left:105px;top:980px;width:360px"></div>
    <div class="row alt" style="left:105px;top:1050px;width:360px"></div>
    <div class="abs" style="left:285px;top:700px;width:1px;height:420px;background:#e2e2e2"></div>
    <div class="cell" style="left:105px;top:700px;width:180px">Stat 1</div><div class="cell" style="left:285px;top:700px;width:180px">0.5</div>
    <div class="cell" style="left:105px;top:770px;width:180px">Stat 2</div><div class="cell" style="left:285px;top:770px;width:180px">-3</div>
    <div class="cell" style="left:105px;top:840px;width:180px">Stat 3</div><div class="cell" style="left:285px;top:840px;width:180px">30%</div>
    <div class="cell" style="left:105px;top:910px;width:180px">Stat 4</div><div class="cell" style="left:285px;top:910px;width:180px">0.5</div>
    <div class="cell" style="left:105px;top:980px;width:180px">Stat 5</div><div class="cell" style="left:285px;top:980px;width:180px">-3</div>
    <div class="cell" style="left:105px;top:1050px;width:180px">Stat 6</div><div class="cell" style="left:285px;top:1050px;width:180px">30%</div>
    <div class="abs track" style="left:465px;top:700px;height:420px"><div class="pill" style="top:25px;height:370px"></div><div class="thumb" style="top:28px"></div></div>
  </div>
  <div class="abs btn run">RUN</div>
  <div class="abs export" style="left:415px;color:#555">
    <svg width="26" height="22" viewBox="0 0 26 22" fill="none" stroke="currentColor" stroke-width="2.2"><path d="M10 5H3v15h17v-6"/><path d="M12 13c2-6 6-8 11-8M18 1l5 4-5 4"/></svg>Export</div>
  <div class="abs export" style="left:1175px">
    <svg width="26" height="22" viewBox="0 0 26 22" fill="none" stroke="currentColor" stroke-width="2.2"><path d="M10 5H3v15h17v-6"/><path d="M12 13c2-6 6-8 11-8M18 1l5 4-5 4"/></svg>Export</div>

  <!-- trades table -->
  <div class="tbl">
    <div class="abs thead" style="left:545px;top:630px;width:720px"></div>
    <div class="cell hcell" style="left:545px;top:630px;width:180px;color:#fff;border-left:0">Open</div>
    <div class="cell hcell" style="left:725px;top:630px;width:180px;color:#fff">Close</div>
    <div class="cell hcell" style="left:905px;top:630px;width:180px;color:#fff">Size</div>
    <div class="cell hcell" style="left:1085px;top:630px;width:180px;color:#fff">Return</div>
    <div class="row plain" style="left:545px;top:700px;width:680px"></div>
    <div class="row alt" style="left:545px;top:770px;width:680px"></div>
    <div class="row plain" style="left:545px;top:840px;width:680px"></div>
    <div class="row alt" style="left:545px;top:910px;width:680px"></div>
    <div class="row plain" style="left:545px;top:980px;width:680px"></div>
    <div class="row alt" style="left:545px;top:1050px;width:680px"></div>
    <div class="abs" style="left:725px;top:700px;width:1px;height:420px;background:#e2e2e2"></div>
    <div class="abs" style="left:905px;top:700px;width:1px;height:420px;background:#e2e2e2"></div>
    <div class="abs" style="left:1085px;top:700px;width:1px;height:420px;background:#e2e2e2"></div>

    <div class="cell" style="left:545px;top:700px;width:180px">2018-04-05</div><div class="cell" style="left:725px;top:700px;width:180px">2018-04-07</div><div class="cell" style="left:905px;top:700px;width:180px">13</div><div class="cell" style="left:1085px;top:700px;width:140px">5%</div>
    <div class="cell" style="left:545px;top:770px;width:180px">2018-04-05</div><div class="cell" style="left:725px;top:770px;width:180px">2018-04-07</div><div class="cell" style="left:905px;top:770px;width:180px">12</div><div class="cell" style="left:1085px;top:770px;width:140px">7%</div>
    <div class="cell" style="left:545px;top:840px;width:180px">2018-04-05</div><div class="cell" style="left:725px;top:840px;width:180px">2018-04-07</div><div class="cell" style="left:905px;top:840px;width:180px">15</div><div class="cell" style="left:1085px;top:840px;width:140px">6%</div>
    <div class="cell" style="left:545px;top:910px;width:180px">2018-04-05</div><div class="cell" style="left:725px;top:910px;width:180px">2018-04-07</div><div class="cell" style="left:905px;top:910px;width:180px">16</div><div class="cell" style="left:1085px;top:910px;width:140px">9%</div>
    <div class="cell" style="left:545px;top:980px;width:180px">2018-04-05</div><div class="cell" style="left:725px;top:980px;width:180px">2018-04-07</div><div class="cell" style="left:905px;top:980px;width:180px">12</div><div class="cell" style="left:1085px;top:980px;width:140px">8%</div>
    <div class="cell" style="left:545px;top:1050px;width:180px">2018-04-05</div><div class="cell" style="left:725px;top:1050px;width:180px">2018-04-07</div><div class="cell" style="left:905px;top:1050px;width:180px">19</div><div class="cell" style="left:1085px;top:1050px;width:140px">6%</div>
    <div class="abs track" style="left:1225px;top:700px;height:420px"><div class="pill" style="top:25px;height:370px"></div><div class="thumb" style="top:28px"></div></div>
  </div>

  <!-- model selection panel -->
  <div class="abs panel"></div>
  <div class="abs handle"></div>
  <div class="abs handle-text"><span>SELECT A MODEL</span></div>
  <svg class="abs handle-btn" width="28" height="28" viewBox="0 0 28 28"><circle cx="14" cy="14" r="12.5" fill="var(--navy)" stroke="#fff" stroke-width="2"/><path d="M20 14H9M13 9l-5 5 5 5" stroke="#fff" stroke-width="2.2" fill="none"/></svg>

  <div class="abs btn mode on" style="left:75px">Mode 1</div>
  <div class="abs btn mode" style="left:265px">Mode 2</div>
  <div class="abs label" style="left:78px;top:309px">Model:</div>
  <div class="abs select">Model name
    <svg style="position:absolute;right:10px;top:11px" width="16" height="9" viewBox="0 0 16 9"><path d="M0 0h16L8 9z" fill="#555"/></svg></div>
  <div class="abs btn select-btn">Select</div>
  <div class="abs btn add">
    <svg width="22" height="22" viewBox="0 0 22 22" fill="none" stroke="#fff" stroke-width="1.6"><circle cx="11" cy="11" r="9.5"/><path d="M11 6v10M6 11h10"/></svg>ADD A MODEL</div>
  <div class="abs label" style="left:205px;top:450px">Parameters:</div>
  <div class="abs label" style="left:78px;top:490px">Entry:</div>
  <div class="abs field" style="top:485px">0.5</div>
  <div class="abs label" style="left:78px;top:535px">Exit:</div>
  <div class="abs field" style="top:530px">-0.3</div>
  <div class="abs label" style="left:78px;top:580px">Lookback:</div>
  <div class="abs field" style="top:575px">5</div>
</div>
</body>
</html>
```